Create a proposal + product powerpoint

Please see the powerpoint for the slides. There are about 20 slides to be created. Rest of them are for reference and show the design that I like.

I would like to move fast on this, since I need to present it next week (in the week of April 21st).

Please download the current content from here:
https://www.parcelbrook.net/fetch/qRtVmXzLwPkNbYcD

Please make at least 4 slides with the specific content so I can assess your design style.

Target Market(s)

Business Audience and very senior technical audience
Decision Makers

Industry/Entity Type

Product

Colors
e34297
a64599

Requirements
Must have
• Should be very clean, crisp.

I like to use Icons as shown in the powerpoint.... Please see the appendix of the slide deck that shows the various icons. Most of them just have plain text, and I would like to organize so that it does not look like some is just reading text.

I would like to focus on the design aspects so that the audience is clear on how the solution works.

Every page should some graphic element based on the slides shown in the appendix.

```html
<!DOCTYPE html>
<html lang="en">
<head>
<meta charset="utf-8">
<title>Platform Adoption</title>
<link rel="stylesheet" href="https://fonts.googleapis.com/css2?family=Open+Sans:wght@400;600&family=Saira+Semi+Condensed:wght@400&display=swap">
<style>
  :root {
    --page-bg: #efedee;
    --footer-bg: #ffffff;
    --footer-rule: #a9a9a9;
    --ink-dark: #3b3b3b;
    --ink-title-grey: #6f6f6f;
    --accent-pink: #e34297;
    --accent-purple: #a64599;
    --bar-rose: #ea66ad;
    --bar-orchid: #ef86be;
    --bar-blush: #f5b8d9;
    --bar-grey: #8c8c8c;
    --bar-dark-grey: #777777;
    --axis: #2b2b2b;
  }
  * { margin: 0; padding: 0; box-sizing: border-box; }
  html, body { width: 1200px; height: 900px; overflow: hidden; }
  body { background: var(--page-bg); font-family: "Open Sans", Arial, sans-serif; }
  .slide { position: relative; width: 1200px; height: 900px; }
  .title-marker { position: absolute; left: 0; top: 33px; width: 15px; height: 63px; background: #000; }
  .slide-title {
    position: absolute; left: 26px; top: 30px;
    font-family: "Saira Semi Condensed", "Arial Narrow", sans-serif;
    font-weight: 400; font-size: 56px; line-height: 1;
    color: var(--ink-title-grey);
  }
  .slide-title .highlight { color: var(--accent-pink); }
  .slide-subtitle {
    position: absolute; left: 63px; top: 136px;
    font-size: 21px; font-weight: 600; color: var(--ink-dark);
  }
  .chart { position: absolute; left: 0; top: 0; }
  .chart text { font-family: "Open Sans", Arial, sans-serif; font-size: 17px; fill: var(--ink-dark); }
  .footer {
    position: absolute; left: 0; top: 807px; width: 1200px; height: 93px;
    background: var(--footer-bg); border-top: 2px solid var(--footer-rule);
  }
  .copyright {
    position: absolute; right: 14px; top: 32px;
    font-family: "Saira Semi Condensed", "Arial Narrow", sans-serif;
    font-size: 22px; color: var(--ink-dark);
  }
</style>
</head>
<body>
<main class="slide">
  <div class="title-marker"></div>
  <h1 class="slide-title"><span class="highlight">PLATFORM</span> ADOPTION</h1>
  <p class="slide-subtitle">Deployments per quarter show steady growth and a sharp rise after the 2.0 release</p>

  <svg class="chart" width="1200" height="900" viewBox="0 0 1200 900" role="img" aria-label="Bar chart of deployments per quarter">
    <g class="y-labels" text-anchor="end">
      <text x="249" y="267">500+ deployments</text>
      <text x="249" y="337">400 deployments</text>
      <text x="249" y="429">300 deployments</text>
      <text x="249" y="544">200 deployments</text>
      <text x="249" y="677">Pilot stage</text>
    </g>
    <g class="bars">
      <rect x="262" y="534" width="50" height="142" fill="var(--bar-grey)"/>
      <rect x="325" y="420" width="62" height="256" fill="var(--accent-pink)"/>
      <rect x="402" y="465" width="60" height="211" fill="var(--bar-rose)"/>
      <rect x="475" y="550" width="61" height="126" fill="var(--bar-orchid)"/>
      <rect x="555" y="639" width="63" height="37" fill="var(--bar-blush)"/>
      <rect x="631" y="664" width="74" height="12" fill="var(--bar-dark-grey)"/>
      <rect x="717" y="274" width="60" height="402" fill="var(--accent-purple)"/>
      <rect x="790" y="637" width="67" height="39" fill="var(--bar-rose)"/>
      <rect x="868" y="657" width="64" height="19" fill="var(--bar-rose)"/>
    </g>
    <g class="axes" stroke="var(--axis)" stroke-width="1.5">
      <line x1="263" y1="235" x2="263" y2="677"/>
      <line x1="262" y1="677" x2="1023" y2="677"/>
    </g>
    <g class="x-labels">
      <text x="260" y="716">Early access phase</text>
      <text x="521" y="716">General availability</text>
      <text x="838" y="716">Version 2.0 launch</text>
    </g>
  </svg>

  <footer class="footer">
    <p class="copyright">© Product proposal deck</p>
  </footer>
</main>
</body>
</html>
```